Main Street Chat w/Marnie Volk (podcast)

Podcast graphic to attract listeners interested in small business tax, bookkeeping and payroll issues. Main Street Chat w/Marnie Volk. Simple, clever and clear. Bold colors that attract attention and make small business owners interested in listening to her and wanting to get to know her. We want to her to appear to be a coach and expert on small business.

Target Market(s)

women and men in small business

Industry/Entity Type

Business Consultant

Font styles to use
Sans Serif

Colors
b260a6
f78f20
32a6d7

Requirements
Must have
• Warm and inviting, positive and uplifting. Promote a personable lady ready and willing to loyally serve her clients and help them succeed in business.
Nice to have
• Clever and smart attracting people that want her business service and advice.
• Emphasize her warmness and open personality.
Should not have
• Nasty or inappropriate,

```html
<!DOCTYPE html>
<html lang="en">
<head>
<meta charset="utf-8">
<title>Main Street Chat w/ Marnie Volk</title>
<link rel="stylesheet" href="https://fonts.googleapis.com/css2?family=Righteous&family=Lato:wght@700&display=swap">
<style>
  :root {
    --page: #ffffff;
    --cover-deep: #064a74;
    --cover-mid: #0b5a86;
    --cover-dark: #063c5f;
    --portrait-tone: #1a6f86;
    --accent-orange: #f7a325;
    --accent-orange-deep: #e88a1c;
    --title-fill: #0a4c77;
    --network-white: #ffffff;
  }
  * { margin: 0; padding: 0; box-sizing: border-box; }
  html, body {
    width: 1200px;
    height: 1122px;
    overflow: hidden;
    background: var(--page);
  }
  .canvas {
    position: relative;
    width: 1200px;
    height: 1122px;
  }
  .cover {
    position: absolute;
    left: 110px;
    top: 71px;
    width: 980px;
    height: 980px;
    overflow: hidden;
    background: linear-gradient(160deg, var(--cover-mid) 0%, var(--cover-deep) 55%, var(--cover-dark) 100%);
  }
  .cover-portrait {
    position: absolute;
    left: 200px;
    top: 20px;
    width: 560px;
    height: 760px;
    border-radius: 50% 50% 40% 40%;
    background: radial-gradient(ellipse at 55% 45%, var(--portrait-tone) 0%, rgba(26,111,134,0.45) 45%, rgba(11,90,134,0) 75%);
  }
  .network-name {
    position: absolute;
    top: 112px;
    left: 0;
    width: 100%;
    display: flex;
    justify-content: center;
    align-items: center;
    gap: 16px;
    font-family: "Lato", sans-serif;
    font-weight: 700;
    font-size: 30px;
    letter-spacing: 6px;
    color: var(--network-white);
    padding-left: 40px;
  }
  .network-dot {
    width: 22px;
    height: 22px;
    border-radius: 50%;
    background: var(--network-white);
  }
  .show-title {
    position: absolute;
    left: 0;
    width: 100%;
    text-align: center;
    font-family: "Righteous", sans-serif;
    color: var(--title-fill);
    -webkit-text-stroke: 10px var(--accent-orange);
    paint-order: stroke fill;
    text-shadow: 0 4px 6px rgba(0,0,0,0.35);
    line-height: 1;
  }
  .show-title--top {
    top: 520px;
    font-size: 112px;
    letter-spacing: 10px;
  }
  .show-title--main {
    top: 640px;
    font-size: 200px;
    letter-spacing: 6px;
  }
  .host-byline {
    position: absolute;
    top: 848px;
    left: 0;
    width: 100%;
    text-align: center;
    font-family: "Righteous", sans-serif;
    font-size: 76px;
    letter-spacing: 3px;
    color: var(--accent-orange);
    line-height: 1;
  }
</style>
</head>
<body>
  <div class="canvas">
    <section class="cover">
      <div class="cover-portrait" role="img" aria-label="Blue-toned portrait photo of host Marnie Volk smiling"></div>
      <div class="network-name"><span class="network-dot"></span>CLEARVIEW COLLECTIVE PODCAST</div>
      <h1>
        <span class="show-title show-title--top">MAIN STREET</span>
        <span class="show-title show-title--main">CHAT</span>
      </h1>
      <p class="host-byline">W/ MARNIE VOLK</p>
    </section>
  </div>
</body>
</html>
```